Business Cards for IT Consulting Company (Managed Service Provider)

I am looking to have some business cards printed and would like some designs. We are an IT Consulting company based in Vancouver BC. I would like a nice clean and modern look to the cards. I have uploaded all the versions of my logo so parts can be used as needed. Here is a snippit from our website homepage:

Quillbrook Networks Ltd. is an IT Solutions Partner located in Vancouver BC, Canada. We offer IT solutions and support to customers in the greater Vancouver Area. With expertise in Microsoft platforms, as well as Linux and Mac OSX and over 12 years experience in the IT industry, Quillbrook Networks is dedicated to offering our clients top quality service and products. We take pride in the solutions we offer our customers. The greatest compliment a client can give us is to recommend our services.

Quillbrook Networks Ltd. offers a wide range of IT services from onsite service to remote support and managed service solutions. This allows clients to choose the support path that best suits their company’s needs. Supporting many different sized companies from small to enterprise level over the past 12 years Quillbrook Networks has the experience and expertise needed to ensure things run smoothly. Allowing our clients to focus on doing business.

Revolutionizing the way IT services are delivered.

Quillbrook Networks is dedicated to providing our clients with IT solutions that work and grow with them for years to come. This philosophy helps save money in the long run instead of replacing equipment constantly. Far too often IT solutions are not well thought out and while possibly solving the problem at hand, require replacement due to growth or quality within a very short time frame. Quillbrook Networks takes pride in providing solutions that will last and be able to accommodate growth without the need for replacement.

Industry/Entity Type

Information Technology

Contact Information for Business Card

Quillbrook Networks Ltd.
(Employee Name)
Eml: (Employees Email Address)
Web: quillbrook.me
Ph: 604-555-0148

Font styles to use
Serif
Sans Serif

Requirements
Must have
• The Company logo and company colors.
Nice to have
• - Our tag line: "Revolutionizing IT Services" or "Revolutionizing the way IT services are delivered."
• - Also I really like the idea of nature and technology together blending which is sort of where my logo came from so integrating that somehow onto the business cards would be great.

```html
<!DOCTYPE html>
<html lang="en">
<head>
<meta charset="utf-8">
<title>Quillbrook Networks Ltd. – Business Card</title>
<link rel="stylesheet" href="https://fonts.googleapis.com/css2?family=Source+Sans+3:wght@400;600;700&display=swap">
<style>
  :root {
    --stage: #ececec;
    --card: #f3f3f4;
    --brand-blue: #1a93d2;
    --ink-grey: #4a4b4d;
    --rule-grey: #9a9a9c;
    --pattern-tint: #dbe9f2;
    --pattern-tint-2: #eef3f7;
  }
  * { box-sizing: border-box; margin: 0; padding: 0; }
  html, body {
    width: 1105px; height: 1200px; overflow: hidden;
    background: var(--stage);
    font-family: "Source Sans 3", Arial, sans-serif;
  }
  .canvas { position: relative; width: 1105px; height: 1200px; }
  .card {
    position: absolute; left: 182px; width: 747px; height: 426px;
    background: var(--card); overflow: hidden;
  }
  .card--front { top: 120px; }
  .card--back { top: 637px; }

  /* Front */
  .brand-name {
    position: absolute; top: 212px; left: 0; width: 100%;
    transform: translateY(-100%);
    display: flex; align-items: center; justify-content: center; gap: 16px;
    color: var(--brand-blue); font-weight: 600; font-size: 46px; letter-spacing: 0.5px;
  }
  .brand-name__square { width: 34px; height: 34px; background: var(--brand-blue); }
  .person {
    position: absolute; top: 226px; right: 383px; text-align: right;
    color: var(--ink-grey); font-size: 19.5px; line-height: 29px;
  }
  .person__name { color: var(--brand-blue); font-weight: 600; font-size: 30px; line-height: 36px; margin-bottom: 4px; }
  .divider {
    position: absolute; left: 380px; top: 232px; width: 1px; height: 88px;
    background: var(--rule-grey);
  }
  .contact { position: absolute; left: 405px; top: 233px; list-style: none; color: var(--ink-grey); font-size: 19.5px; }
  .contact__item { display: flex; align-items: center; gap: 12px; height: 29px; }
  .contact__icon { width: 17px; height: 17px; fill: var(--brand-blue); flex: none; }
  .wave { position: absolute; left: 0; bottom: 0; width: 100%; height: 90px; }

  /* Back */
  .pattern-field {
    position: absolute; inset: 0;
    background: radial-gradient(ellipse at center, var(--pattern-tint-2) 0%, var(--pattern-tint) 100%);
  }
  .back-mark {
    position: absolute; top: 175px; left: 0; width: 100%; text-align: center;
    color: var(--brand-blue); font-weight: 600; font-size: 36px;
  }
  .tagline {
    position: absolute; top: 337px; left: 0; width: 100%; text-align: center;
    color: var(--ink-grey); font-weight: 600; font-size: 20px;
  }
</style>
</head>
<body>
<main class="canvas">
  <section class="card card--front" aria-label="Card front">
    <div class="brand-name"><span class="brand-name__square"></span><span>Quillbrook Networks Ltd.</span></div>

    <div class="person">
      <p class="person__name">Daniel Harper</p>
      <p>4120 Alder Crescent</p>
      <p>Burnaby, BC V5G 1K2</p>
    </div>
    <div class="divider"></div>
    <ul class="contact">
      <li class="contact__item">
        <svg class="contact__icon" viewBox="0 0 24 24"><path d="M6.6 10.8a15.1 15.1 0 0 0 6.6 6.6l2.2-2.2c.3-.3.7-.4 1-.2 1.1.4 2.3.6 3.6.6.6 0 1 .4 1 1V20c0 .6-.4 1-1 1A17 17 0 0 1 3 4c0-.6.4-1 1-1h3.5c.6 0 1 .4 1 1 0 1.3.2 2.5.6 3.6.1.3 0 .7-.2 1z"/></svg>
        <span>604-555-0148</span>
      </li>
      <li class="contact__item">
        <svg class="contact__icon" viewBox="0 0 24 24"><path d="M2 5h20v14H2z M3 6l9 7 9-7" fill="var(--brand-blue)"/><path d="M3 6.5l9 6.5 9-6.5" fill="none" stroke="#f3f3f4" stroke-width="1.6"/></svg>
        <span>dharper@quillbrook.me</span>
      </li>
      <li class="contact__item">
        <svg class="contact__icon" viewBox="0 0 24 24"><circle cx="12" cy="12" r="10"/><path d="M2 12h20M12 2c3 3 3 17 0 20M12 2c-3 3-3 17 0 20" fill="none" stroke="#f3f3f4" stroke-width="1.5"/></svg>
        <span>www.quillbrook.me</span>
      </li>
    </ul>

    <svg class="wave" viewBox="0 0 747 90" preserveAspectRatio="none" aria-hidden="true">
      <path d="M0 90 L0 66 C160 44 330 58 470 60 C600 62 690 40 747 10 L747 90 Z" fill="var(--brand-blue)"/>
      <path d="M0 58 C140 28 310 26 470 42 C590 54 680 34 730 4 C690 38 600 58 470 54 C320 46 150 44 0 66 Z" fill="var(--ink-grey)"/>
    </svg>
  </section>

  <section class="card card--back" aria-label="Card back">
    <div class="pattern-field" role="img" aria-label="Faint light-blue repeating geometric background pattern"></div>
    <p class="back-mark">Quillbrook Networks Ltd.</p>
    <p class="tagline">Revolutionizing IT Services</p>
  </section>
</main>
</body>
</html>
```